Blow Dry Bar Business Cards

These cards must be eye catching and modern.
You must be willing to work fast and make changes.

Winner will be offered other projects

Files 1 THIS IS THE STYLE CARDS I AM INTRESTED IN!!!
Please be creative, I am paying for my own eye catching design. I need files to be nexa press ready.

COLORS THAT ARE PAINTED INSIDE MY SHOP:
- - - http://www.quorvelpaint.example/en/explore-colors/painter/color-selector.html?colors=4007-3C

- - - http://www.brandivex.example/color/paint-colors/hidden-corridor-d58-2

I want the business cards sleek and modern if you use the logo please correct imperfections. I added the part that says Blow Dry Bar (see website).
Do not be afraid to separate the blow dryer from the name to make the cards look like the file with the pink elephant.

SHOULD INCLUDE
*Blow Dryer (we are a blow dry bar not a salon we do not cut or color so do not include sheers of any kind)
*BUSINESS NAME: Simply Swept Upward - Blow Dry Bar (PLEASE SEE MY WEBSITE)
* Website: SIMPLYSWEPTUPWARD.EXAMPLE
*Phone number (555) 014-2763
Updates

Nexa press said it can be submitted in JPG

http://www.brandivex.example/color/paint-colors/hidden-corridor-d58-2 http://www.quorvelpaint.example/en/explore-colors/painter/color-selector.html?colors=4007-3C ^^^^ These links will take you to the color paint that is painted inside my shop.

Target Market(s)

AGES 18 - 55 WOMEN
HIGH END MARKET

Industry/Entity Type

Salon

Requirements
Must have
• SEE COLOR EXAMPLE FILE
BLOW DRYER
UNIQUE
I LIKE THE CARD WITH THE PINK ELEPHANT THE BEST
Nice to have
• BE AS CREATIVE AND MODERN AS POSSIBLE DO NOT COPY ANY OF THE CARDS BELOW.
Should not have
• SCISSORS
PINK

```html
<!DOCTYPE html>
<html lang="en">
<head>
<meta charset="utf-8">
<title>Swept Upward – Business Cards</title>
<link rel="stylesheet" href="https://fonts.googleapis.com/css2?family=Arvo&family=Lato:wght@400;700&display=swap">
<style>
  :root {
    --teal: #5bc2cb;
    --teal-deep: #49aeb8;
    --white: #ffffff;
    --paper: #fdfdfd;
    --brown: #3b2a26;
    --stage: #2b2b2d;
  }
  * { margin: 0; padding: 0; box-sizing: border-box; }
  html, body { width: 1200px; height: 800px; overflow: hidden; }
  body {
    background: var(--stage);
    font-family: "Lato", sans-serif;
    position: relative;
  }
  .card {
    position: absolute;
    top: 252px;
    width: 520px;
    height: 297px;
    border-radius: 22px;
    overflow: hidden;
  }
  /* Back side */
  .card--back { left: 60px; background: var(--teal); color: var(--white); }
  .card--back .wordmark {
    position: absolute; top: 78px; left: 0; width: 100%;
    text-align: center;
    font-family: "Arvo", serif; font-size: 28px; color: var(--white);
  }
  .card--back .address {
    position: absolute; left: 36px; top: 178px;
    font-size: 15px; line-height: 1.3;
  }
  .contact-list {
    position: absolute; left: 36px; top: 232px;
    list-style: none; font-size: 15px; line-height: 1.45;
  }
  .contact-list li { display: flex; align-items: center; gap: 8px; }
  .contact-list svg { width: 13px; height: 13px; fill: var(--white); }

  /* Front side */
  .card--front { left: 620px; background: var(--paper); }
  .card--front .shapes { position: absolute; inset: 0; }
  .person {
    position: absolute; left: 96px; top: 108px; color: var(--white);
  }
  .person .name { font-size: 19px; font-weight: 400; }
  .person .role { font-size: 14px; margin-top: 4px; margin-left: 4px; }
  .brand-dot {
    position: absolute; left: 410px; top: 92px;
    width: 58px; height: 58px; border-radius: 50%;
    background: var(--teal);
  }
  .brand {
    position: absolute; right: 48px; top: 178px; text-align: right;
  }
  .brand .wordmark {
    font-family: "Arvo", serif; font-size: 44px; color: var(--teal);
    line-height: 1;
  }
  .brand .tagline {
    font-size: 19px; color: var(--brown); margin-top: 2px;
  }
  .brand .service {
    font-size: 14px; color: var(--brown);
  }
</style>
</head>
<body>

  <section class="card card--back" aria-label="Business card, back">
    <p class="wordmark">Swept Upward</p>
    <p class="address">210 Harbor Bend Road Suite 4 Millbrook,<br>texas 70000</p>
    <ul class="contact-list">
      <li>
        <svg viewBox="0 0 16 16" aria-hidden="true"><path d="M3 1h3l1.5 4-2 1.2a9 9 0 0 0 4.3 4.3L11 8.5l4 1.5v3a2 2 0 0 1-2 2A12 12 0 0 1 1 3a2 2 0 0 1 2-2z"/></svg>
        (555) 014-2763
      </li>
      <li>
        <svg viewBox="0 0 16 16" aria-hidden="true"><path d="M8 0a8 8 0 1 0 0 16A8 8 0 0 0 8 0zm5.9 7h-2.9a12 12 0 0 0-1-4.8A6 6 0 0 1 13.9 7zM8 2c.7 1 1.3 2.8 1.5 5h-3C6.7 4.8 7.3 3 8 2zM6 2.2A12 12 0 0 0 5 7H2.1A6 6 0 0 1 6 2.2zM2.1 9H5a12 12 0 0 0 1 4.8A6 6 0 0 1 2.1 9zM8 14c-.7-1-1.3-2.8-1.5-5h3c-.2 2.2-.8 4-1.5 5zm2 .8a12 12 0 0 0 1-4.8h2.9a6 6 0 0 1-3.9 4.8z"/></svg>
        WWW.SIMPLYSWEPTUPWARD.EXAMPLE
      </li>
    </ul>
  </section>

  <section class="card card--front" aria-label="Business card, front">
    <svg class="shapes" viewBox="0 0 520 297" aria-hidden="true">
      <defs>
        <filter id="soft-shadow" x="-20%" y="-20%" width="140%" height="140%">
          <feDropShadow dx="0" dy="3" stdDeviation="4" flood-color="#000" flood-opacity="0.25"/>
        </filter>
      </defs>
      <path class="top-band" fill="var(--teal)"
        d="M0,0 H520 V18 C455,8 420,45 380,85 C330,135 270,150 210,140 C140,128 60,140 0,175 Z"/>
      <path class="hollow" fill="var(--white)" filter="url(#soft-shadow)"
        d="M0,140 C40,100 110,70 190,72 C150,100 100,150 60,205 C35,210 15,215 0,218 Z"/>
      <path class="name-leaf" fill="var(--teal)"
        d="M6,175 C50,120 120,84 190,80 C240,78 250,110 205,138 C160,166 90,190 30,205 C14,208 4,192 6,175 Z"/>
    </svg>
    <div class="person">
      <p class="name">Dana Merrow</p>
      <p class="role">Owner</p>
    </div>
    <span class="brand-dot" aria-hidden="true"></span>
    <div class="brand">
      <p class="wordmark">Swept Upward</p>
      <p class="tagline">Simply Swept Upward</p>
      <p class="service">Blow Dry Bar</p>
    </div>
  </section>

</body>
</html>
```